English and Spanish Language School Needs a Business Card

Need a business card design a startup company called Maribel Language School. The company will offer English and Spanish conversational level courses designed to make the learner feel comfortable with grammar and vocabulary. We would like to see a logo with some colour that should communicate learning, growth.

Target Market(s)

Consumers and businesses

Industry/Entity Type

Education

Contact Information for Business Card

TBD

Font styles to use
Serif

Requirements
Must have
• Include the following
• Logo
• Name
• Title
• Cellphone Number
• Office Phone number
• Email address
• Office Address

```html
<!DOCTYPE html>
<html lang="en">
<head>
<meta charset="utf-8">
<title>Maribel Language School – Business Card</title>
<link href="https://fonts.googleapis.com/css2?family=Open+Sans:wght@400;600;700&display=swap" rel="stylesheet">
<style>
  :root {
    --brand-red: #c8202a;
    --ink: #2a2a2a;
    --paper: #ffffff;
    --backdrop: #ecebe8;
  }
  * { margin: 0; padding: 0; box-sizing: border-box; }
  html, body {
    width: 1200px; height: 900px; overflow: hidden;
    background: var(--backdrop);
    font-family: "Open Sans", Arial, sans-serif;
  }
  .stage { position: relative; width: 1200px; height: 900px; }
  .card {
    position: absolute;
    width: 540px; height: 308px;
    border-radius: 2px;
    box-shadow: 0 6px 18px rgba(0,0,0,0.18);
  }
  .card-front {
    left: 70px; top: 130px;
    background: var(--brand-red);
    display: flex; align-items: center; justify-content: center;
  }
  .card-back {
    left: 590px; top: 460px;
    background: var(--paper);
  }
  .brand-name {
    font-weight: 700;
    line-height: 1.05;
    text-align: center;
  }
  .card-front .brand-name { color: var(--paper); font-size: 44px; }
  .card-front .brand-name small { display: block; font-size: 20px; font-weight: 700; }
  .card-back .brand-name {
    position: absolute; right: 28px; top: 26px;
    color: var(--brand-red); font-size: 30px;
  }
  .card-back .brand-name small { display: block; font-size: 13px; font-weight: 700; }
  .rule {
    position: absolute; left: 0; right: 0; height: 2px;
    background: var(--brand-red);
  }
  .rule-top { top: 108px; }
  .rule-bottom { top: 196px; }
  .holder { position: absolute; left: 28px; top: 130px; }
  .holder-name { color: var(--brand-red); font-weight: 700; font-size: 18px; }
  .holder-title { color: var(--ink); font-size: 14px; margin-top: 2px; }
  .contacts {
    position: absolute; right: 24px; top: 124px;
    list-style: none; text-align: right;
    color: var(--ink); font-size: 12px; line-height: 19px;
  }
  .contacts li { display: flex; align-items: center; justify-content: flex-end; gap: 5px; }
  .contacts svg { width: 10px; height: 10px; fill: var(--brand-red); }
  .address {
    position: absolute; left: 40px; top: 226px;
    color: var(--ink); font-size: 16px; line-height: 24px; font-style: normal;
  }
</style>
</head>
<body>
<main class="stage">
  <section class="card card-front" aria-label="Business card front">
    <p class="brand-name">Maribel<small>Language School</small></p>
  </section>

  <section class="card card-back" aria-label="Business card back">
    <p class="brand-name">Maribel<small>Language School</small></p>
    <div class="rule rule-top"></div>
    <div class="holder">
      <p class="holder-name">Daniel Reyes</p>
      <p class="holder-title">Managing Director</p>
    </div>
    <ul class="contacts">
      <li>(055) 318 204 776
        <svg viewBox="0 0 10 10" aria-hidden="true"><path d="M1 3 Q5 0 9 3 L8 4.5 L6.5 4 L6.5 3 Q5 2.6 3.5 3 L3.5 4 L2 4.5 Z M2.5 5 H7.5 L8.5 9 H1.5 Z"/></svg>
      </li>
      <li>(055)640912358
        <svg viewBox="0 0 10 10" aria-hidden="true"><rect x="2.5" y="0.5" width="5" height="9" rx="1"/><rect x="3.5" y="1.8" width="3" height="5.5" fill="#fff"/></svg>
      </li>
      <li>hello@maribelschool.com
        <svg viewBox="0 0 10 10" aria-hidden="true"><rect x="0.5" y="2" width="9" height="6.5" rx="0.8"/><path d="M1 2.6 L5 5.6 L9 2.6" stroke="#fff" stroke-width="0.9" fill="none"/></svg>
      </li>
    </ul>
    <div class="rule rule-bottom"></div>
    <address class="address">48, Calle Olivar Norte,<br>Sevilla, 41003</address>
  </section>
</main>
</body>
</html>
```